Personal Web page for recruiter and owner of consulting firm

I work full time as a recruiter so I want a page that allows for me to support my efforts. I would like a long single page, I need to be able to upload four two minute videos, and 4 images. I also want the color scheme to match with my consulting company. I own the domain marcusfenwold.net already through wordpress . I took a shot at it myself and its terrible.

Target Market(s)

Potential clients

Industry/Entity Type

Management Consulting

Logo Text

marcus fenwold

Font styles to use
Serif

Requirements
Must have
• Must in color scheme go well with my consulting company logo attached
• Must be able to upload 4 two minute videos and 4 images (photos of me)
• Single long scroll page
• Modern and clean
Nice to have
• Easy for me to update videos images and text without complex coding
Should not have
• I want the design and feel to go well with my logos not exactly replicate it

```html
<!DOCTYPE html>
<html lang="en">
<head>
<meta charset="utf-8">
<title>Marcus Fenwold</title>
<link href="https://fonts.googleapis.com/css2?family=Lora:wght@500;600;700&family=Source+Serif+4:wght@400;600;700&display=swap" rel="stylesheet">
<style>
:root{
  --navy:#0c2a5b;
  --navy-deep:#0a2350;
  --sky:#6bb3ea;
  --button-blue:#4aa2e8;
  --ink:#1d2b44;
  --muted:#7b8494;
  --panel:#f2f3f6;
  --white:#ffffff;
  --photo-office:linear-gradient(135deg,#8a97a8 0%,#c9d1db 45%,#6f7f93 100%);
  --photo-warm:linear-gradient(135deg,#b9a58d 0%,#e3ddd4 50%,#8f8f93 100%);
  --photo-cool:linear-gradient(135deg,#3d5675 0%,#9fb2c8 55%,#2f3f55 100%);
}
*{margin:0;padding:0;box-sizing:border-box}
html,body{width:1200px;height:3672px;overflow:hidden}
body{position:relative;background:var(--white);font-family:"Source Serif 4",Georgia,serif;color:var(--ink)}
.abs{position:absolute}
h1,h2,h3{font-family:"Lora",Georgia,serif;font-weight:500}
.section-title{color:var(--navy);font-size:30px;text-align:center}
.divider{display:flex;align-items:center;justify-content:center;gap:6px;margin-top:10px}
.divider span{display:block;width:40px;height:1px;background:#9aa6b8}
.divider i{display:block;width:5px;height:5px;border-radius:50%;background:var(--button-blue)}
.divider.left{justify-content:flex-start}
.body-text{font-size:13px;line-height:21px;color:var(--muted)}
.centered{text-align:center}
.photo{border-radius:2px}
.video{position:absolute}
.play{position:absolute;left:50%;top:50%;width:46px;height:32px;margin:-16px 0 0 -23px;border-radius:7px;background:rgba(10,20,40,.85)}
.play:after{content:"";position:absolute;left:18px;top:9px;border-left:13px solid #fff;border-top:7px solid transparent;border-bottom:7px solid transparent}
.btn{display:inline-block;font-size:14px;font-weight:600;padding:0 22px;height:40px;line-height:40px;border-radius:2px;color:#fff}

/* header + hero */
.hero{left:0;top:0;width:1200px;height:632px;background:var(--photo-office)}
.hero-shade{left:0;top:0;width:1200px;height:632px;background:linear-gradient(180deg,rgba(12,42,91,.35),rgba(12,42,91,.15))}
.topbar{left:0;top:0;width:1200px;height:96px;background:rgba(12,42,91,.92)}
.brand{left:92px;top:30px;font-family:"Lora",serif;font-weight:600;font-size:24px;letter-spacing:1px;color:#fff}
.nav{left:464px;top:38px;display:flex;gap:38px;font-size:15px;color:#fff;align-items:flex-start}
.nav a.active{border-bottom:2px solid #fff;padding-bottom:6px}
.hero-title{left:0;top:282px;width:1200px;text-align:center;font-size:50px;line-height:62px;color:#fff;text-shadow:0 2px 6px rgba(0,0,0,.3)}
.hero-actions{left:0;top:428px;width:1200px;display:flex;justify-content:center;gap:22px}
.btn-get{background:var(--button-blue)}
.btn-post{background:#a9d3f5;color:var(--navy)}
.dots{left:0;top:580px;width:1200px;display:flex;justify-content:center;gap:8px}
.dots i{width:9px;height:9px;border-radius:50%;background:rgba(255,255,255,.6)}
.dots i:first-child{background:#fff}

/* what we do */
.services-panel{left:0;top:1228px;width:628px;height:384px;background:var(--panel)}
.service{display:flex;flex-direction:column;align-items:flex-start;gap:10px;font-size:14px;font-weight:600;color:var(--navy)}

/* call band */
.call-left{left:0;top:2660px;width:600px;height:224px;background:var(--navy);color:#fff;text-align:center}
.call-right{left:600px;top:2660px;width:600px;height:224px;background:var(--sky);text-align:center}
.call-left h2{font-size:34px;margin-top:40px}
.call-right h2{font-size:30px;margin-top:44px;color:var(--navy)}

/* footer */
.footer{left:0;top:3328px;width:1200px;height:344px;background:var(--navy-deep);color:#fff}
.footer h3{font-weight:600;font-size:16px}
.footer ul{list-style:none;font-size:12.5px;line-height:22px;color:#c8d2e2;margin-top:14px}
.social{display:flex;gap:22px}
.social i{width:16px;height:16px;border-radius:50%;background:#fff;display:block}
</style>
</head>
<body>

<!-- Hero -->
<div class="abs hero" role="img" aria-label="Business team meeting in a bright office"></div>
<div class="abs hero-shade"></div>
<div class="abs topbar"></div>
<div class="abs brand">marcus fenwold</div>
<nav class="abs nav">
  <a class="active">Home</a><a>About Us</a><a>Services</a><a>Testimonials</a><a>Team</a><a>Contact</a>
  <svg width="16" height="16" viewBox="0 0 16 16" aria-hidden="true" style="margin-top:3px"><circle cx="6.5" cy="6.5" r="5" fill="none" stroke="#fff" stroke-width="2"/><line x1="10.5" y1="10.5" x2="15" y2="15" stroke="#fff" stroke-width="2"/></svg>
</nav>
<h1 class="abs hero-title">More Than 500 Employees Placed<br>Every Year</h1>
<div class="abs hero-actions"><a class="btn btn-get">Get Job</a><a class="btn btn-post">Post Job</a></div>
<div class="abs dots"><i></i><i></i><i></i><i></i></div>

<!-- Welcome -->
<div class="abs" style="left:0;top:668px;width:1200px">
  <h2 class="section-title">Welcome To Marcus Fenwold</h2>
  <div class="divider"><span></span><i></i><span></span></div>
</div>
<p class="abs body-text centered" style="left:150px;top:740px;width:900px">I help growing companies find the right people and shape the right plans. I listen first, study your market, and then build a hiring and growth path that fits your goals. From first call to final placement I stay close, share clear updates, and measure every result so you always know where your business stands today.</p>
<div class="video photo" style="left:152px;top:888px;width:428px;height:272px;background:var(--photo-warm)" role="img" aria-label="Video: consultants discussing a plan at a table"><span class="play"></span></div>
<div class="video photo" style="left:628px;top:888px;width:420px;height:272px;background:var(--photo-cool)" role="img" aria-label="Video: consultant speaking at an office window"><span class="play"></span></div>

<!-- What we do -->
<div class="abs services-panel"></div>
<div class="abs" style="left:100px;top:1276px;width:440px">
  <h2 class="section-title" style="text-align:left">What We Do</h2>
  <div class="divider left"><span></span><i></i><span></span></div>
  <p class="body-text" style="margin-top:18px">We match skilled people with growing firms and guide leaders through change with simple, proven steps. Every plan is shaped around your team, your budget and your timeline.</p>
  <div style="display:flex;gap:90px;margin-top:40px">
    <div class="service">
      <svg width="22" height="24" viewBox="0 0 22 24" aria-hidden="true"><circle cx="11" cy="6" r="5" fill="#0c2a5b"/><path d="M1 24c0-7 4-11 10-11s10 4 10 11z" fill="#0c2a5b"/></svg>
      Permanent Staffing
    </div>
    <div class="service">
      <svg width="26" height="24" viewBox="0 0 26 24" aria-hidden="true"><circle cx="7" cy="6" r="4" fill="#0c2a5b"/><circle cx="19" cy="6" r="4" fill="#0c2a5b"/><path d="M0 24c0-6 3-10 7-10s7 4 7 10zM12 24c0-6 3-10 7-10s7 4 7 10z" fill="#0c2a5b"/></svg>
      Consulting Services
    </div>
  </div>
  <div class="divider left" style="margin-top:44px;margin-left:100px"><i style="background:#9aa6b8"></i><i style="background:#9aa6b8"></i><i style="background:#9aa6b8"></i></div>
</div>
<div class="abs photo" style="left:628px;top:1240px;width:572px;height:368px;background:var(--photo-cool)" role="img" aria-label="Portrait photo of the consultant"></div>

<!-- Special -->
<div class="video photo" style="left:100px;top:1680px;width:520px;height:368px;background:var(--photo-office)" role="img" aria-label="Video: consultant working on a laptop"><span class="play"></span></div>
<div class="abs" style="left:664px;top:1722px;width:460px">
  <h2 class="section-title" style="text-align:left;font-size:26px;white-space:nowrap">What Special In Our Consulting</h2>
  <div class="divider left"><span></span><i></i><span></span></div>
  <p class="body-text" style="margin-top:18px">My advice is practical and built on years of hands-on hiring work across many industries. I know what makes a team succeed, and I share that knowledge openly. Each client gets a single point of contact, honest feedback, clear pricing and a plan that keeps moving until the goals are reached and the new people are settled in.</p>
  <a class="btn" style="background:var(--navy);margin-top:26px">Know More</a>
</div>

<!-- Process -->
<div class="abs" style="left:0;top:2120px;width:1200px">
  <h2 class="section-title">Our Consulting Process Make Your Business Easy</h2>
  <div class="divider"><span></span><i></i><span></span></div>
</div>
<p class="abs body-text" style="left:150px;top:2200px;width:900px">We start with a short discovery call to learn how your business works. Next we review your current team, map the roles you need and set simple targets. Then we search, screen and present strong candidates while guiding your leaders on structure and growth. After each placement we check in often to make sure the fit is right and the results keep coming for your company.</p>
<div class="abs photo" style="left:152px;top:2332px;width:428px;height:288px;background:var(--photo-warm)" role="img" aria-label="Desk with laptop, notebook and an apple"></div>
<div class="abs photo" style="left:628px;top:2332px;width:420px;height:288px;background:var(--photo-office)" role="img" aria-label="Team reviewing charts in a meeting"></div>

<!-- Call band -->
<div class="abs call-left">
  <h2>Call Us @ 555 0142 7731</h2>
  <p style="font-size:13px;line-height:20px;width:440px;margin:12px auto 0;color:#d6deeb">Talk with me today about your hiring needs and get a clear plan for your next steps.</p>
  <a class="btn" style="background:var(--button-blue);margin-top:18px">Call Now</a>
</div>
<div class="abs call-right">
  <h2>Request A Call Back</h2>
  <p style="font-size:13px;line-height:20px;width:440px;margin:12px auto 0;color:var(--navy)">Leave your details and I will reach out to you personally within one business day.</p>
  <a class="btn" style="background:var(--navy);margin-top:18px">Request A Call</a>
</div>

<!-- Testimonials -->
<div class="video photo" style="left:100px;top:2960px;width:400px;height:328px;background:var(--photo-cool)" role="img" aria-label="Video: client testimonial"><span class="play"></span></div>
<div class="abs" style="left:560px;top:2976px;width:540px;text-align:center">
  <h2 class="section-title" style="font-size:28px">What Our Client Says About Us</h2>
  <div class="divider"><span></span><i></i><span></span></div>
  <p class="body-text" style="margin-top:18px">Hear from leaders who trusted me with their hiring and growth. They share how I found great people fast, kept them informed at every step and helped their businesses reach new goals with less stress.</p>
  <a class="btn" style="background:var(--navy);margin-top:28px">Check For More Video</a>
</div>

<!-- Footer -->
<footer class="abs footer">
  <div class="abs" style="left:100px;top:52px"><h3>Get In Touch</h3></div>
  <div class="abs social" style="left:300px;top:55px"><i></i><i></i><i></i><i></i></div>
  <div class="abs" style="left:980px;top:54px;font-size:12.5px;display:flex;gap:8px;align-items:center">
    <svg width="14" height="12" viewBox="0 0 14 12" aria-hidden="true"><path d="M0 6L14 0 10 12 7 8z" fill="#fff"/></svg>Send Us Feedback
  </div>
  <div class="abs" style="left:100px;top:96px;width:1000px;height:1px;background:rgba(255,255,255,.25)"></div>
  <div class="abs" style="left:100px;top:156px;font-family:'Lora',serif;font-weight:600;font-size:24px;letter-spacing:1px">marcus fenwold</div>
  <div class="abs" style="left:400px;top:128px"><h3>Company</h3>
    <ul><li>Team</li><li>Careers</li><li>Terms &amp; Conditions</li><li>Privacy Policy</li><li>Gallery</li></ul></div>
  <div class="abs" style="left:624px;top:128px"><h3>Site Map</h3>
    <ul><li>Home</li><li>About Us</li><li>Services</li><li>Testimonials</li><li>Contact Us</li></ul></div>
  <div class="abs" style="left:820px;top:128px;width:280px"><h3>Newsletter</h3>
    <div style="display:flex;margin-top:16px"><div style="flex:1;height:30px;background:#fff;color:#8a93a3;font-size:11.5px;line-height:30px;padding-left:10px">enter your email</div><div style="width:40px;height:30px;background:var(--button-blue)"></div></div>
    <p style="font-size:11.5px;color:#c8d2e2;margin-top:12px">Subscribe our latest news, offers and discounts</p>
  </div>
  <p class="abs" style="left:0;top:316px;width:1200px;text-align:center;font-size:10.5px;color:#a9b5c9">Copyright © Marcus Fenwold. All Rights Reserved.</p>
</footer>

</body>
</html>
```